Steadfast Greenwell HEMP Cannabis CBD tinctures

We need packaging for our line of CBD product label design based in Oakland Ca Brand is called 'Steadfast Greenwell'. Our initial product is tincture to help people with pain with out the High effect of THC. I will be attaching og other company sample. The design should communicate slick look and relay health. Use the logo as way to color

Target Market(s)

CBD

Font styles to use
Serif
Decorative

Requirements
Must have
• Design that will make it stand out from the rest of the product on the shelve and be bright.
Nice to have
• The package must be able to stand out and not be dominated by Black color the green color must be the main color.
Should not have
• Be all black and get lost on the shelves

```html
<!DOCTYPE html>
<html lang="en">
<head>
<meta charset="utf-8">
<title>Steadfast Greenwell – CBD Tincture Label</title>
<link rel="stylesheet" href="https://fonts.googleapis.com/css2?family=Montserrat:wght@400;500;700&family=Oswald:wght@600&display=swap">
<style>
  :root {
    --backdrop: #fdfdc9;
    --label-white: #f7f8f7;
    --pattern-tint: #eef4ee;
    --green: #47c25a;
    --green-bright: #3ec14f;
    --green-deep: #25933a;
    --green-pale: #b9eebd;
    --green-soft: #93d8a0;
    --rule-grey: #9a9a9a;
    --cbd-green: #2fa443;
  }
  * { box-sizing: border-box; margin: 0; padding: 0; }
  html, body {
    width: 1200px; height: 1200px; overflow: hidden;
    background: var(--backdrop);
  }
  .canvas {
    position: relative; width: 1200px; height: 1200px;
    background: var(--backdrop);
  }
  .label {
    position: absolute; left: 180px; top: 72px;
    width: 840px; height: 1056px;
    background: var(--label-white);
    overflow: hidden;
    box-shadow: 0 6px 24px rgba(0,0,0,0.08);
  }
  .label__pattern {
    position: absolute; left: 0; top: 38px; right: 0; bottom: 0;
    background: linear-gradient(180deg, var(--pattern-tint), var(--label-white) 60%, var(--pattern-tint));
  }
  .label__top-band {
    position: absolute; left: 0; top: 0; width: 100%; height: 30px;
    background: var(--green);
    border-bottom: 8px solid #d9dcd9;
    height: 38px;
  }
  .label__tab {
    position: absolute; left: 295px; top: 38px;
    width: 252px; height: 58px;
    background: var(--green);
    border-radius: 0 0 8px 8px;
    color: #fff;
    font: 400 36px/58px "Montserrat", sans-serif;
    text-align: center; letter-spacing: -0.5px;
  }
  .brand {
    position: absolute; left: 0; right: 0; top: 150px;
    text-align: center;
  }
  .brand__mark {
    display: block; margin: 0 auto 44px;
    width: 150px; height: 150px;
    background: var(--green);
    border-radius: 10px;
  }
  .brand__name {
    font: 700 52px/1 "Montserrat", sans-serif;
    color: var(--green);
    letter-spacing: -1px;
  }
  .strength {
    position: absolute; left: 234px; top: 569px;
    width: 386px; height: 64px;
    background: var(--green);
    color: #fff;
    font: 700 46px/64px "Montserrat", sans-serif;
    text-align: center;
  }
  .rule {
    position: absolute; left: 234px; width: 386px; height: 3px;
    background: var(--rule-grey);
  }
  .rule--upper { top: 667px; }
  .rule--lower { top: 728px; }
  .extract {
    position: absolute; left: 0; right: 0; top: 674px;
    text-align: center;
    font: 500 44px/52px "Montserrat", sans-serif;
    color: var(--green);
    letter-spacing: 1px;
  }
  .product {
    position: absolute; left: 0; right: 0; top: 736px;
    text-align: center;
    font: 600 112px/1.1 "Oswald", sans-serif;
    color: var(--cbd-green);
    transform: scaleX(0.85);
  }
  .label__base {
    position: absolute; left: 0; bottom: 0;
    width: 840px; height: 190px;
  }
</style>
</head>
<body>
<main class="canvas">
  <section class="label">
    <div class="label__pattern" role="img" aria-label="Faint hexagonal cube pattern in pale green"></div>
    <div class="label__top-band"></div>
    <div class="label__tab">TINCTURE</div>

    <div class="brand">
      <span class="brand__mark"></span>
      <p class="brand__name">Steadfast Greenwell</p>
    </div>

    <div class="strength">1500MG</div>
    <div class="rule rule--upper"></div>
    <p class="extract">HEMP EXTRACT</p>
    <div class="rule rule--lower"></div>
    <p class="product">CBD</p>

    <svg class="label__base" viewBox="0 0 840 190" aria-hidden="true">
      <rect x="0" y="78" width="420" height="112" fill="var(--green-pale)"/>
      <rect x="420" y="78" width="420" height="112" fill="var(--green-soft)"/>
      <polygon points="207,36 420,0 420,190 207,190" fill="var(--green-bright)"/>
      <polygon points="420,0 650,36 650,190 420,190" fill="var(--green-deep)"/>
    </svg>
  </section>
</main>
</body>
</html>
```